Software Development Consulting Company Needs Business Card Design

We need a new business card design for our consultants at Kestrel Works (kestrelworks.example). We are a small firm that provides high-end software development and methodology consulting to medium to large enterprise IT organizations.

Our logo uses Futura for the font and we would like to stick with navy blue and canary yellow for the logo colors. Attached are normal and reversed versions of our logos in illustrator format.
Updates

Hi Everyone, Thank yo very much for your amazing design ideas. I have created a poll for this project and our employees will be voting on the design they wish to use. We will be making a decision this Wednesday (October 22nd). Thanks again, Dale Hartwick

Industry/Entity Type

Business

```html
<!DOCTYPE html>
<html lang="en">
<head>
<meta charset="utf-8">
<title>Kestrel Works – Business Card</title>
<link rel="stylesheet" href="https://fonts.googleapis.com/css2?family=Jost:wght@400&family=Lato:wght@400;700&display=swap">
<style>
  :root {
    --navy: #2b5576;
    --navy-deep: #1f3f5e;
    --canary: #f2e21b;
    --paper: #f3f3f1;
    --backdrop: #e4e4e4;
    --ink: #2a2a2a;
  }
  * { box-sizing: border-box; margin: 0; padding: 0; }
  html, body { width: 1200px; height: 720px; overflow: hidden; }
  body { background: var(--backdrop); position: relative; font-family: "Lato", sans-serif; }

  .card {
    position: absolute;
    top: 242px;
    width: 420px;
    height: 238px;
    background: var(--paper);
    overflow: hidden;
  }
  .card--front { left: 147px; }
  .card--back  { left: 633px; }

  .brand-panel {
    position: absolute;
    top: 0;
    width: 128px;
    height: 100%;
    background: linear-gradient(180deg, var(--navy) 0%, var(--navy-deep) 100%);
  }
  .card--front .brand-panel { right: 0; }
  .card--back  .brand-panel { left: 0; }

  .wordmark {
    position: absolute;
    display: flex;
    align-items: center;
    gap: 7px;
  }
  .wordmark__dot {
    width: 8px; height: 8px;
    border-radius: 50%;
    background: var(--canary);
    flex: none;
  }
  .wordmark__name {
    font-family: "Jost", sans-serif;
    font-weight: 400;
    color: var(--navy-deep);
    text-transform: uppercase;
    letter-spacing: 0.14em;
    white-space: nowrap;
  }
  .card--front .wordmark { left: 22px; top: 110px; }
  .card--front .wordmark__name { font-size: 17px; }
  .card--back .wordmark { right: 17px; top: 28px; }
  .card--back .wordmark__name { font-size: 15px; }

  .contact {
    position: absolute;
    right: 17px;
    text-align: right;
    color: var(--ink);
  }
  .contact__name {
    top: 78px;
    font-weight: 700;
    font-size: 13px;
    color: var(--navy-deep);
    letter-spacing: -0.01em;
  }
  .contact__title { top: 95px; font-size: 10px; }
  .contact__lines {
    top: 121px;
    list-style: none;
    font-size: 10px;
    line-height: 12.3px;
  }
  .contact__lines li { display: flex; justify-content: flex-end; align-items: center; gap: 6px; }
  .contact__lines svg { width: 10px; height: 10px; flex: none; }
  .contact__address { top: 190px; font-size: 10px; line-height: 12.3px; font-style: normal; padding-right: 2px; }
</style>
</head>
<body>

<section class="card card--front" aria-label="Card front">
  <div class="wordmark">
    <span class="wordmark__dot"></span>
    <span class="wordmark__name">Kestrel Works</span>
  </div>
  <div class="brand-panel"></div>
</section>

<section class="card card--back" aria-label="Card back">
  <div class="brand-panel"></div>
  <div class="wordmark">
    <span class="wordmark__dot"></span>
    <span class="wordmark__name">Kestrel Works</span>
  </div>

  <p class="contact contact__name">Dale Hartwick</p>
  <p class="contact contact__title">Principal Consultant</p>

  <ul class="contact contact__lines">
    <li>555-010-4567
      <svg viewBox="0 0 10 10" aria-hidden="true"><path d="M1 3.5 Q5 0.5 9 3.5 L8 5 L6.5 4 V3 H3.5 V4 L2 5 Z M2.5 6 H7.5 L8.5 9 H1.5 Z" fill="var(--navy-deep)"/></svg>
    </li>
    <li>dale.hartwick@kestrelworks.example
      <svg viewBox="0 0 10 10" aria-hidden="true"><rect x="0.5" y="2" width="9" height="6.5" fill="var(--navy-deep)"/><path d="M0.5 2 L5 5.8 L9.5 2" fill="none" stroke="#fff" stroke-width="0.8"/></svg>
    </li>
    <li>@dalehart
      <svg viewBox="0 0 10 10" aria-hidden="true"><rect x="1" y="1.5" width="8" height="5.5" fill="none" stroke="var(--navy-deep)" stroke-width="1.2"/><rect x="3" y="8" width="4" height="1" fill="var(--navy-deep)"/></svg>
    </li>
    <li>www.kestrelworks.example
      <svg viewBox="0 0 10 10" aria-hidden="true"><rect x="0.5" y="0.5" width="9" height="9" rx="1.5" fill="var(--navy-deep)"/><circle cx="5" cy="5" r="2.6" fill="none" stroke="#fff" stroke-width="0.8"/></svg>
    </li>
  </ul>

  <address class="contact contact__address">2450 Harbor View Dr,<br>Fairmont, MO 63000</address>
</section>

</body>
</html>
```